Thornvale Group needs a business card design

We need a new business card design using the logo recently selected in a logo competition on Pixel Bazaar. Our business is a consultancy specializing in aviation and energy and the winning business card design will promote an image of precision and professionalism with creativity.

Please use the logo with the name on the front of the card and use a complementary font. Make the back white with either the light grey or dark grey logo.

Target Market(s)

Senior finance and legal leaders at aviation and energy companies

Industry/Entity Type

Management Consulting

Contact Information for Business Card

Peter Castrell
President
Thornvale Group

www.thornvalegroup.example

(555) 204-6391
pc@thornvalegroup.example

Requirements
Must have
• Professional font that goes well with the logo font

```html
<!DOCTYPE html>
<html lang="en">
<head>
<meta charset="utf-8">
<title>Thornvale Group – Business Card</title>
<link rel="stylesheet" href="https://fonts.googleapis.com/css2?family=Source+Sans+3:wght@300;400;600;700&display=swap">
<style>
  :root {
    --backdrop: #161616;
    --card-light: #f3f3f3;
    --card-navy: #0f3e6b;
    --card-navy-deep: #0b3358;
    --card-navy-soft: #1a4c7c;
    --ink-navy: #0f3a66;
    --ink-dark: #1e1e1e;
    --ink-white: #ffffff;
    --line-light: rgba(170, 200, 230, 0.55);
  }
  * { margin: 0; padding: 0; box-sizing: border-box; }
  html, body {
    width: 1200px;
    height: 900px;
    overflow: hidden;
    background: var(--backdrop);
    font-family: "Source Sans 3", "Myriad Pro", Arial, sans-serif;
  }
  .stage { position: relative; width: 1200px; height: 900px; }

  .card {
    position: absolute;
    top: 184px;
    width: 302px;
    height: 490px;
    border-radius: 12px;
    overflow: hidden;
    text-align: center;
  }
  .card--front { left: 299px; background: var(--card-light); color: var(--ink-dark); }
  .card--back { left: 646px; width: 304px; background: var(--card-navy); color: var(--ink-white); }

  /* brand mark placeholder: one plain square */
  .brand-square {
    position: absolute;
    top: 228px;
    left: 0;
    right: 0;
    margin: 0 auto;
    width: 64px;
    height: 64px;
    background: var(--ink-navy);
  }
  .card--front .brand-square { top: 46px; }

  .brand-name {
    position: absolute;
    left: 0;
    right: 0;
    font-weight: 300;
    text-transform: uppercase;
  }
  .brand-name__main {
    display: block;
    font-size: 31px;
    line-height: 34px;
    letter-spacing: 0.06em;
  }
  .brand-name__sub {
    display: block;
    margin-top: 4px;
    font-size: 16px;
    line-height: 20px;
    letter-spacing: 1.05em;
    padding-left: 1.05em;
  }
  .card--front .brand-name { top: 146px; color: var(--ink-navy); }
  .card--back .brand-name { top: 298px; color: var(--ink-white); }

  .back-decor {
    position: absolute;
    top: 0;
    left: 0;
    width: 304px;
    height: 290px;
    background: linear-gradient(155deg, var(--card-navy-soft) 0%, var(--card-navy) 45%, var(--card-navy-deep) 75%, var(--card-navy) 100%);
  }
  .back-line {
    position: absolute;
    top: 0;
    left: 0;
  }

  .person { position: absolute; top: 312px; left: 0; right: 0; }
  .person__name {
    font-size: 19px;
    font-weight: 600;
    color: var(--ink-navy);
    line-height: 22px;
  }
  .person__title { font-size: 13px; color: var(--ink-dark); line-height: 16px; }

  .contact {
    position: absolute;
    top: 390px;
    left: 0;
    right: 0;
    list-style: none;
    font-size: 13.5px;
    line-height: 21px;
    color: var(--ink-dark);
  }
  .contact__item { display: flex; justify-content: center; align-items: center; gap: 4px; }
  .contact__icon { width: 10px; height: 10px; fill: var(--ink-navy); }

  .services { position: absolute; top: 388px; left: 0; right: 0; }
  .services__headline { font-size: 18.5px; font-weight: 700; line-height: 24px; }
  .services__sectors {
    margin-top: 4px;
    font-size: 16px;
    font-weight: 600;
    line-height: 24px;
    word-spacing: 2px;
  }
</style>
</head>
<body>
  <main class="stage">
    <section class="card card--front" aria-label="Card front">
      <div class="brand-square" aria-hidden="true"></div>
      <p class="brand-name">
        <span class="brand-name__main">Thornvale</span>
        <span class="brand-name__sub">Group</span>
      </p>
      <div class="person">
        <p class="person__name">Peter Castrell</p>
        <p class="person__title">President</p>
      </div>
      <ul class="contact">
        <li class="contact__item">
          <svg class="contact__icon" viewBox="0 0 10 10" aria-hidden="true"><path d="M2 0.5 L3.6 2.6 L2.8 3.6 C3.4 5 4.8 6.5 6.3 7.2 L7.3 6.3 L9.5 7.9 L8.3 9.5 C4.5 9.2 0.8 5.4 0.5 1.7 Z"/></svg>
          <span>(555) 204-6391</span>
        </li>
        <li class="contact__item">
          <svg class="contact__icon" viewBox="0 0 10 10" aria-hidden="true"><path d="M0 2 H10 V8.5 H0 Z M0.8 2.6 L5 5.6 L9.2 2.6" stroke="#f3f3f3" stroke-width="0.8"/></svg>
          <span>pc@thornvalegroup.example</span>
        </li>
      </ul>
    </section>

    <section class="card card--back" aria-label="Card back">
      <div class="back-decor" role="img" aria-label="Large faint angular brand decoration in deep navy tones"></div>
      <svg class="back-line" width="304" height="290" viewBox="0 0 304 290" aria-hidden="true">
        <line x1="0" y1="154" x2="280" y2="0" stroke="var(--line-light)" stroke-width="1.2"/>
      </svg>
      <p class="brand-name">
        <span class="brand-name__main">Thornvale</span>
        <span class="brand-name__sub">Group</span>
      </p>
      <div class="services">
        <p class="services__headline">Finance and Strategy Consulting</p>
        <p class="services__sectors">Aviation&nbsp;|&nbsp;Manufacturing&nbsp;&nbsp;|&nbsp;Energy</p>
      </div>
    </section>
  </main>
</body>
</html>
```